High Tech Real Estate Startup needs a business card

We are developing an innovative real estate marketing product based around advanced search and virtual reality.

We talk to people, we need business cards.

Target Market(s)

The target market is technology professionals and realtors.

Contact Information for Business Card

The information to be included will include

Name
Title
Phone Number
E-mail Address
www.zelquin.com

It should use simple iconography for each one of those fields.

Font styles to use
Other font styles liked:
• Co, Jubilat, Avenir

Colors

Designer to choose colors to be used in the design.

Requirements
Must have
• Clean aesthetic,
• Good use of negative space.
• It should use our company logo, shown in the attached file. It is able to use the negative of that logo (coloured font and white background) and I have attached other acceptable accent colours in a swatch file.
Should not have
• Should not be too busy
• No extraneous text (slogans, tag lines etc)

```html
<!DOCTYPE html>
<html lang="en">
<head>
<meta charset="utf-8">
<title>Zelquin Business Card</title>
<link href="https://fonts.googleapis.com/css2?family=Nunito+Sans:wght@400;600&display=swap" rel="stylesheet">
<style>
  :root {
    --teal: #08b5b9;
    --white: #ffffff;
    --backdrop: #d3cbb8;
  }
  * { box-sizing: border-box; margin: 0; padding: 0; }
  html, body { width: 1200px; height: 1000px; overflow: hidden; }
  body {
    background: var(--backdrop);
    font-family: "Nunito Sans", "Avenir", sans-serif;
    position: relative;
  }
  .card {
    position: absolute;
    left: 270px;
    width: 658px;
    height: 375px;
    overflow: hidden;
  }
  .card-front { top: 78px; background: var(--white); }
  .card-back { top: 534px; background: var(--teal); color: var(--white); }

  .front-wordmark {
    position: absolute;
    left: 0; right: 0; top: 140px;
    text-align: center;
    font-size: 80px;
    font-weight: 600;
    line-height: 1;
    letter-spacing: 1px;
    color: var(--teal);
  }

  .person-name {
    position: absolute;
    left: 47px; top: 86px;
    font-size: 32px;
    font-weight: 400;
    line-height: 1;
  }
  .person-title {
    position: absolute;
    left: 48px; top: 132px;
    font-size: 19px;
    line-height: 1;
  }
  .divider {
    position: absolute;
    left: 0; top: 183px;
    width: 330px; height: 2px;
    background: var(--white);
  }
  .web-tab {
    position: absolute;
    left: 315px; top: 183px;
    width: 343px; height: 38px;
  }
  .web-address {
    position: absolute;
    left: 345px; right: 0; top: 191px;
    text-align: center;
    font-size: 19px;
    line-height: 1;
    color: var(--teal);
    letter-spacing: 0.3px;
  }
  .contact-list { list-style: none; position: absolute; left: 46px; top: 249px; }
  .contact-item {
    display: flex; align-items: center;
    height: 36px;
    font-size: 21px;
  }
  .contact-icon { width: 18px; height: 18px; margin-right: 23px; fill: var(--white); }
  .back-wordmark {
    position: absolute;
    right: 34px; top: 258px;
    font-size: 60px;
    font-weight: 600;
    line-height: 1;
    letter-spacing: 1px;
  }
</style>
</head>
<body>
  <section class="card card-front">
    <div class="front-wordmark">ZELQUIN</div>
  </section>

  <section class="card card-back">
    <div class="person-name">Name of Person</div>
    <div class="person-title">Title of Person</div>
    <div class="divider"></div>
    <svg class="web-tab" viewBox="0 0 343 38" aria-hidden="true">
      <path d="M0 0 H343 V38 H32 Q21 38 16 28 L4 6 Q1 0 0 0 Z" fill="#ffffff"/>
    </svg>
    <div class="web-address">www.zelquin.com</div>
    <ul class="contact-list">
      <li class="contact-item">
        <svg class="contact-icon" viewBox="0 0 24 24" aria-hidden="true">
          <path d="M6.6 10.8c1.4 2.8 3.8 5.1 6.6 6.6l2.2-2.2c.3-.3.7-.4 1-.2 1.1.4 2.3.6 3.6.6.6 0 1 .4 1 1V20c0 .6-.4 1-1 1C10.6 21 3 13.4 3 4c0-.6.4-1 1-1h3.5c.6 0 1 .4 1 1 0 1.3.2 2.5.6 3.6.1.3 0 .7-.2 1L6.6 10.8z"/>
        </svg>
        <span>+123 456 7890</span>
      </li>
      <li class="contact-item">
        <svg class="contact-icon" viewBox="0 0 24 24" aria-hidden="true">
          <path d="M2 6h20v1.5l-10 6-10-6z M2 9.6l10 6 10-6V19H2z"/>
        </svg>
        <span>E-mail Address</span>
      </li>
    </ul>
    <div class="back-wordmark">ZELQUIN</div>
  </section>
</body>
</html>
```